Tevlora website

Web design for small consulting firm
It can be simple, easy to find approach

The primary use is business to business for

a. people wanting to find out a bit more of us after receiving a business card
b. Search words to draw people from search engines to us

Target Market(s)

Senior staff of large companies, in their work capacity
MD / CEO / CFO , directors, etc.

Industry/Entity Type

Business

Colors
ffffff
f79020
faa54b
33a6d7

```html
<!DOCTYPE html>
<html lang="en">
<head>
<meta charset="utf-8">
<title>Tevlora Insight</title>
<link href="https://fonts.googleapis.com/css2?family=Open+Sans:wght@300;400;600&display=swap" rel="stylesheet">
<style>
:root{
  --white:#ffffff;
  --orange:#f79020;
  --orange-light:#faa54b;
  --blue:#33a6d7;
  --blue-dark:#1a8cc4;
  --ink:#222222;
  --text:#444444;
  --muted:#888888;
  --line:#e6e6e6;
  --card:#fbfbfb;
  --footer:#474747;
  --footer-text:#9a9a9a;
}
*{margin:0;padding:0;box-sizing:border-box}
html,body{width:729px;height:1200px;overflow:hidden;background:var(--white)}
body{position:relative;font-family:"Open Sans",Arial,sans-serif;color:var(--text)}
.abs{position:absolute}

/* header */
.brand{left:105px;top:26px;font-size:20px;font-weight:600;color:var(--blue);letter-spacing:.3px}
.callout{left:450px;top:38px;font-size:7.5px;color:var(--ink)}
.social{left:561px;top:33px;display:flex;gap:4px}
.social span{width:18px;height:18px;border-radius:50%;background:var(--blue-dark)}

/* nav */
.nav{left:105px;top:81px;width:520px;height:34px;background:linear-gradient(var(--blue),var(--blue-dark));display:flex;align-items:center;font-size:7.5px;color:var(--white)}
.nav .home{width:50px;height:100%;background:var(--orange);display:flex;align-items:center;justify-content:center}
.nav a{position:absolute;color:var(--white);text-decoration:none}

/* hero */
.hero{left:105px;top:115px;width:520px;height:277px;background:linear-gradient(100deg,#f4f7fa 0%,#e6edf3 45%,#c9d6e2 75%,#aebccb 100%);border:1px solid var(--line)}
.hero-title{left:139px;top:193px;font-size:32px;color:var(--orange);font-weight:400;letter-spacing:.5px}
.hero-sub{left:139px;font-size:19px;color:var(--ink);font-weight:400}
.dots{left:142px;top:303px;display:flex;gap:4px}
.dots span{width:6px;height:6px;border-radius:50%;background:var(--ink);border:1px solid var(--white)}
.dots span:first-child{background:var(--orange)}

/* feature cards */
.feature{top:412px;width:162px;height:194px;background:var(--card);border:1px solid var(--line);text-align:center}
.feature h3{margin-top:13px;font-size:12.5px;font-weight:400;color:var(--ink)}
.feature .icon{width:66px;height:66px;margin:10px auto 0;border-radius:50%;border:1px solid #e2e2e2;background:radial-gradient(circle,#f3dca0 0%,#fff 70%)}
.feature p{margin:18px 10px 0;font-size:5.8px;line-height:11.4px;color:var(--ink)}
.btn{display:inline-block;background:var(--orange);color:var(--white);font-size:8.5px;border-radius:2px}
.feature .btn{margin-top:10px;width:44px;height:20px;line-height:20px}

/* sections */
.section-title{top:629px;font-size:10.5px;color:var(--ink)}
.section-title em{font-style:normal;color:var(--orange)}
.rule{top:654px;height:1px;background:var(--line)}
.welcome-media{left:105px;top:669px;width:246px;height:115px;border:2px solid #eee;background:linear-gradient(110deg,#f2f2f2 0%,#dbe5ee 50%,#c2d2e0 100%)}
.articles{left:104px;top:802px;font-size:8.5px;color:var(--ink)}
.article-body{left:104px;top:827px;width:247px;font-size:5.8px;line-height:11.5px;color:var(--ink)}
.learn{left:105px;top:898px;width:59px;height:23px;line-height:23px;text-align:center;font-size:7px}

/* news */
.news{left:376px;width:249px;height:112px;background:var(--card);border:1px solid var(--line)}
.news .thumb{position:absolute;left:11px;top:11px;width:83px;height:61px;border:2px solid #eee;background:linear-gradient(135deg,#7e93ab,#c8d3de)}
.news h4{position:absolute;left:105px;top:12px;font-size:7px;font-weight:400;color:var(--ink)}
.news time{position:absolute;left:105px;top:33px;font-size:5.5px;color:var(--ink)}
.news p{position:absolute;left:105px;top:48px;width:134px;font-size:5.8px;line-height:11.5px;color:var(--ink);text-align:justify}
.news .read{position:absolute;right:12px;top:95px;font-size:5.5px;color:var(--blue)}

/* partners + footer */
.footer{left:0;top:966px;width:729px;height:234px;background:var(--footer)}
.partners{left:104px;top:940px;width:521px;height:53px;background:var(--white);border:1px solid var(--line);display:flex;align-items:center;justify-content:space-around;padding:0 10px}
.partners span{width:72px;height:18px;border-radius:3px;background:#d8d8d8}
.foot-head{top:1016px;font-size:9px;color:#d0d0d0;font-weight:400}
.foot-text{font-size:5.8px;line-height:11.5px;color:var(--footer-text)}
.contact-row{left:294px;display:flex;align-items:flex-start;gap:10px;font-size:6.8px;line-height:11px;color:var(--footer-text)}
.signup{left:466px;top:1092px;display:flex;height:26px}
.signup .field{width:115px;background:var(--white);font-size:6px;color:var(--ink);padding-left:6px;line-height:26px}
.signup .go{width:45px;background:var(--blue);color:var(--white);font-size:9.5px;line-height:26px;text-align:center}
.copyright{left:105px;top:1171px;font-size:5.8px;color:var(--footer-text)}
.foot-icons{left:362px;top:1168px;display:flex;gap:6px}
.foot-icons span{width:12px;height:12px;border-radius:50%;background:#e8e8e8}
.foot-links{left:516px;top:1171px;font-size:5.8px;color:var(--footer-text);word-spacing:2px}
</style>
</head>
<body>

<div class="abs brand">Tevlora Insight</div>
<div class="abs callout">CALL US +1 800 555 0147</div>
<div class="abs social"><span></span><span></span><span></span></div>

<nav class="abs nav">
  <div class="home">HOME</div>
  <a style="left:73px">Who we are</a>
  <a style="left:153px">Our values</a>
  <a style="left:225px">Our Clients</a>
  <a style="left:300px">What we do</a>
  <a style="left:375px">Contact us</a>
</nav>

<div class="abs hero" role="img" aria-label="Photo of two business colleagues working together at a laptop"></div>
<div class="abs hero-title">WE KNOW</div>
<div class="abs hero-sub" style="top:236px">EVERYTHING ABOUT</div>
<div class="abs hero-sub" style="top:266px">SUCCESSFUL BUSINESS</div>
<div class="abs dots"><span></span><span></span><span></span><span></span></div>

<section class="abs feature" style="left:105px">
  <h3>Who we are</h3>
  <div class="icon" role="img" aria-label="Gold figure illustration"></div>
  <p>Lorem ipsum DOLOR sit amet, consectetur adipisicing elit, sed do eiusmod tempor et dolore magna aliqua.Lorem ipsum DOLOR sit amet,</p>
  <span class="btn">More</span>
</section>
<section class="abs feature" style="left:284px">
  <h3>What we do</h3>
  <div class="icon" role="img" aria-label="Gold figure with key illustration"></div>
  <p>Lorem ipsum DOLOR sit amet, consectetur adipisicing elit, sed do eiusmod tempor et dolore magna aliqua.Lorem ipsum DOLOR sit amet,</p>
  <span class="btn">More</span>
</section>
<section class="abs feature" style="left:463px">
  <h3>Our Clients</h3>
  <div class="icon" role="img" aria-label="Gold figure illustration"></div>
  <p>Lorem ipsum DOLOR sit amet, consectetur adipisicing elit, sed do eiusmod tempor et dolore magna aliqua.Lorem ipsum DOLOR sit amet,</p>
  <span class="btn">More</span>
</section>

<h2 class="abs section-title" style="left:104px;font-weight:400">Welcome To <em>Tevlora Insight Ltd</em></h2>
<h2 class="abs section-title" style="left:375px;font-weight:400">News &amp; <em>events</em></h2>
<div class="abs rule" style="left:104px;width:247px"></div>
<div class="abs rule" style="left:375px;width:250px"></div>

<div class="abs welcome-media" role="img" aria-label="Photo of a tablet showing charts held during a meeting"></div>
<div class="abs articles">Articles and publications</div>
<p class="abs article-body">Lorem ipsum dolor sit amet, consectetuer adipiscing elit, sed diam nonummy nibh euismod tincidunt ut laoreet dolore magna aliquam erat volutpat. Ut wisi enim ad minim veniam, quis nostrud exerci tation ullamcorper suscipit.Lorem ipsum dolor sit amet, consectetuer adipiscing elit, sed diam nonummy nibh euismod tincidunt ut laoreet dolore magna aliquam erat volutpat.</p>
<span class="abs btn learn">Learn More</span>

<article class="abs news" style="top:670px">
  <div class="thumb" role="img" aria-label="Photo of a team meeting"></div>
  <h4>Financial Management Insight</h4>
  <time>March-22-2011</time>
  <p>Lorem ipsum dolor sit amet, consectetuer adipiscing elit, sed diam nonummy nibh euismod tincidunt ut laoreet dolore magna aliquam erat volutpat.</p>
  <span class="read">Read More</span>
</article>
<article class="abs news" style="top:798px">
  <div class="thumb" role="img" aria-label="Photo of colleagues shaking hands"></div>
  <h4>Information Technology Insight</h4>
  <time>March-22-2011</time>
  <p>Lorem ipsum dolor sit amet, consectetuer adipiscing elit, sed diam nonummy nibh euismod tincidunt ut laoreet dolore magna aliquam erat volutpat.</p>
  <span class="read">Read More</span>
</article>

<footer class="abs footer"></footer>
<div class="abs partners"><span></span><span></span><span></span><span></span><span></span></div>

<h3 class="abs foot-head" style="left:105px">ABOUT US</h3>
<h3 class="abs foot-head" style="left:293px">ADDRESS</h3>
<h3 class="abs foot-head" style="left:466px">NEWSLETTER</h3>

<p class="abs foot-text" style="left:105px;top:1047px;width:158px">Lorem ipsum dolor sit amet, consct etuer adipiscing elit, sed diam nonummy nibh euismod tincidunt ut laoreet dol ore magna aliquam erat volutpat. Ut wisi enim ad minimveniam.Lorem ipsum dolor sit amet, consct etuer adipiscing elit, sed diam nonummy nibh euismod tincidunt ut laoreet dol ore magna aliquam erat volutpat. Ut wsi enim ad minimveniam.</p>

<div class="abs contact-row" style="top:1048px">
  <svg width="10" height="14" viewBox="0 0 10 14"><path d="M5 0a5 5 0 0 1 5 5c0 3.5-5 9-5 9S0 8.5 0 5a5 5 0 0 1 5-5z" fill="#1e1e1e"/><circle cx="5" cy="5" r="1.8" fill="#474747"/></svg>
  <span style="width:130px">Po Box 20417, Harbour Lane, Ashford, 4820</span>
</div>
<div class="abs contact-row" style="top:1084px">
  <svg width="10" height="16" viewBox="0 0 10 16"><rect x=".5" y=".5" width="9" height="15" rx="1.5" fill="#1e1e1e"/><rect x="2" y="2.5" width="6" height="9" fill="#5a5a5a"/></svg>
  <span style="padding-top:2px">Call us: 021 555 0182</span>
</div>
<div class="abs contact-row" style="top:1116px">
  <svg width="12" height="9" viewBox="0 0 12 9"><rect width="12" height="9" fill="#1e1e1e"/><path d="M0 0l6 5 6-5" stroke="#6a6a6a" fill="none"/></svg>
  <span style="margin-top:-2px">info@tevlora.co.nz</span>
</div>

<p class="abs foot-text" style="left:466px;top:1047px;width:160px">Excepteur sint occaecat cupidatat non proident, sunt in culpa qui officia deserunt mollit anim id est laborum.</p>
<div class="abs signup"><div class="field">Enter Email</div><div class="go">Sign Up</div></div>

<div class="abs copyright">Copyright © 2014 Tevlora Insight Ltd . All rights reserved</div>
<div class="abs foot-icons"><span></span><span></span><span></span><span></span></div>
<div class="abs foot-links">Home | About | Services | Contact</div>

</body>
</html>
```